Business Card Re-Design/Update

We'd like to update out business cards. I've included our current "Style guide" which has the colour scheme of the organisation in it. I've also included the branding files with logos etc in them.

I've also included a copy of one of our existing cards so that you can see how ugly/dated they look. I'd like a fresh modern corporate look.

Target Market(s)

These are for our clients, potential clients, industry contacts - like all business cards

Contact Information for Business Card

Name
Position
Company Address - Level 1, 47 Fernby Street, Carlow Qld 4072
Direct Phone
mobile
Email
Website -www.korvalit.com.au
Logo

Colors

Designer to choose colors to be used in the design.

Requirements
Must have
• Main Logo
• Cards will need to be editable to be able to personalize them for each new employee.
Nice to have
• The MapOut, ShipWell, KeepSteady would be okay to have if they can be sensibly and professionally added to the look without detracting from the main imagery.
• Maybe they could go on the back of the card? will leave this to your creative discretion as to whether/where they fit.
Should not have
• Should not have decorative or script fonts

```html
<!DOCTYPE html>
<html lang="en">
<head>
<meta charset="utf-8">
<title>korvalit business card</title>
<link href="https://fonts.googleapis.com/css2?family=Roboto:wght@400;500;700&family=Roboto+Condensed:wght@700&display=swap" rel="stylesheet">
<style>
  :root {
    --backdrop: #e4e4e4;
    --paper: #f2f2f2;
    --brand-red: #c4161c;
    --brand-red-deep: #8e0a10;
    --brand-red-light: #d41c23;
    --ink: #231f20;
    --stripe: #0a0a0a;
    --white: #ffffff;
  }
  * { margin: 0; padding: 0; box-sizing: border-box; }
  html, body { width: 1200px; height: 960px; overflow: hidden; }
  body {
    background: var(--backdrop);
    font-family: "Roboto", Arial, sans-serif;
    position: relative;
  }
  .card {
    position: absolute;
    width: 600px;
    height: 343px;
    overflow: hidden;
    box-shadow: 0 2px 4px rgba(0,0,0,0.25);
  }
  .card--front { left: 314px; top: 113px; background: var(--paper); }
  .card--back {
    left: 311px; top: 472px;
    background: radial-gradient(ellipse at 45% 45%, var(--brand-red-light) 0%, var(--brand-red) 40%, var(--brand-red-deep) 100%);
  }
  .front-shapes { position: absolute; inset: 0; }

  .wordmark {
    position: absolute;
    display: flex;
    align-items: center;
    gap: 12px;
  }
  .wordmark__square {
    width: 34px; height: 34px;
    background: var(--brand-red);
  }
  .wordmark__name {
    font-weight: 700;
    color: var(--ink);
    letter-spacing: -0.5px;
    line-height: 1;
  }
  .card--front .wordmark { left: 46px; top: 55px; }
  .card--front .wordmark__name { font-size: 34px; }

  .contact {
    position: absolute;
    right: 32px;
    top: 94px;
    text-align: right;
    color: var(--white);
  }
  .contact__name {
    font-family: "Roboto Condensed", "Arial Narrow", sans-serif;
    font-weight: 700;
    font-size: 20px;
    letter-spacing: 0.3px;
    line-height: 24px;
  }
  .contact__role { font-size: 14px; line-height: 18px; }
  .contact__address { margin-top: 18px; font-size: 14px; line-height: 18px; }
  .contact__lines { margin-top: 8px; list-style: none; }
  .contact__line {
    display: flex;
    justify-content: flex-end;
    align-items: center;
    gap: 8px;
    font-size: 14px;
    line-height: 19px;
  }
  .contact__line svg { width: 13px; height: 13px; flex: none; }

  .card--back .wordmark { left: 50%; top: 128px; transform: translateX(-50%); gap: 16px; }
  .card--back .wordmark__square { width: 56px; height: 56px; background: var(--white); }
  .card--back .wordmark__name { font-size: 60px; color: var(--white); }

  .services {
    position: absolute;
    left: 46px;
    right: 60px;
    top: 278px;
    display: flex;
    justify-content: space-between;
    list-style: none;
  }
  .service {
    display: flex;
    align-items: center;
    gap: 8px;
    color: var(--white);
    font-weight: 500;
    font-size: 26px;
    line-height: 1;
  }
  .service__square { width: 22px; height: 22px; background: var(--white); }
</style>
</head>
<body>

<section class="card card--front" aria-label="Card front">
  <svg class="front-shapes" viewBox="0 0 600 343" width="600" height="343" aria-hidden="true">
    <defs>
      <radialGradient id="redGlow" cx="0.62" cy="0.45" r="0.7">
        <stop offset="0" stop-color="#d41c23"/>
        <stop offset="0.5" stop-color="#c4161c"/>
        <stop offset="1" stop-color="#8e0a10"/>
      </radialGradient>
    </defs>
    <polygon points="406,0 421,0 168,343 153,343" fill="#0a0a0a"/>
    <polygon points="426,0 600,0 600,343 173,343" fill="url(#redGlow)"/>
  </svg>

  <div class="wordmark">
    <span class="wordmark__square"></span>
    <span class="wordmark__name">korvalit</span>
  </div>

  <div class="contact">
    <p class="contact__name">MAREN HOLT</p>
    <p class="contact__role">Business Development Manager</p>
    <p class="contact__address">Level 1, 47 Fernby Street<br>Carlow Qld 4072</p>
    <ul class="contact__lines">
      <li class="contact__line">+61 (0)7 3000 4821
        <svg viewBox="0 0 16 16" aria-label="phone"><path fill="#fff" d="M3.6 1.2l2.3 2.6-1.2 1.9c.8 1.9 2.4 3.6 4.3 4.5l1.9-1.2 2.6 2.3-1.4 2.6C7 13.6 2.4 9 1.1 2.7z"/></svg></li>
      <li class="contact__line">+61 (0)7 3000 4837
        <svg viewBox="0 0 16 16" aria-label="phone"><path fill="#fff" d="M3.6 1.2l2.3 2.6-1.2 1.9c.8 1.9 2.4 3.6 4.3 4.5l1.9-1.2 2.6 2.3-1.4 2.6C7 13.6 2.4 9 1.1 2.7z"/></svg></li>
      <li class="contact__line">+61 (0)400 615 290
        <svg viewBox="0 0 16 16" aria-label="mobile"><rect x="4" y="1" width="8" height="14" rx="1.5" fill="none" stroke="#fff" stroke-width="1.6"/><circle cx="8" cy="12.3" r="0.9" fill="#fff"/></svg></li>
      <li class="contact__line">+61 (0)7 3000 4809
        <svg viewBox="0 0 16 16" aria-label="fax"><rect x="4" y="2" width="8" height="5" fill="#fff"/><rect x="1" y="7" width="14" height="7" rx="1" fill="#fff"/><rect x="4" y="10" width="8" height="1.3" fill="#c4161c"/></svg></li>
      <li class="contact__line">mholt@korvalit.com.au
        <svg viewBox="0 0 16 16" aria-label="email"><rect x="1" y="3" width="14" height="10" fill="#fff"/><path d="M1.5 3.5L8 9l6.5-5.5" fill="none" stroke="#c4161c" stroke-width="1.2"/></svg></li>
      <li class="contact__line">www.korvalit.com.au
        <svg viewBox="0 0 16 16" aria-label="website"><circle cx="8" cy="8" r="7" fill="#fff"/><path d="M5 4.5c1.5.5 2 1.8 1 2.8s.5 2.2 1.6 2.4M10 3.5c-.6 1.2.4 2 1.6 2.2M9.5 12c.3-1.2 1.3-1.8 2.4-1.5" fill="none" stroke="#c4161c" stroke-width="1.3"/></svg></li>
    </ul>
  </div>
</section>

<section class="card card--back" aria-label="Card back">
  <div class="wordmark">
    <span class="wordmark__square"></span>
    <span class="wordmark__name">korvalit</span>
  </div>
  <ul class="services">
    <li class="service"><span class="service__square"></span>MapOut</li>
    <li class="service"><span class="service__square"></span>ShipWell</li>
    <li class="service"><span class="service__square"></span>KeepSteady</li>
  </ul>
</section>

</body>
</html>
```